Automotive Accessories Business Card

Design a business template that match our new logo design and our industry.

https://www.qelmotorgear.com/

Target Market(s)

Aftermarket auto parts and accessories

Industry/Entity Type

automotive

Contact Information for Business Card

company logo

Font styles to use
Serif
Sans Serif

Colors
EB3D1F
EC4F4E
F09395
F8D3D4
FCEDEE

```html
<!DOCTYPE html>
<html lang="en">
<head>
<meta charset="utf-8">
<title>QEL Motor Gear – Business Card</title>
<link rel="stylesheet" href="https://fonts.googleapis.com/css2?family=Montserrat:wght@400;500;700&display=swap">
<style>
  :root {
    --bg: #e6e6e6;
    --card-white: #ffffff;
    --card-dark: #3d3d3f;
    --red: #d71f26;
    --ink: #3a3a3a;
    --rule: #555555;
  }
  * { margin: 0; padding: 0; box-sizing: border-box; }
  html, body { width: 1200px; height: 802px; overflow: hidden; }
  body {
    background: var(--bg);
    font-family: "Montserrat", Arial, sans-serif;
    color: var(--ink);
    position: relative;
  }
  .card {
    position: absolute;
    width: 540px;
    height: 309px;
    border-bottom: 4px solid var(--red);
    box-shadow: 0 6px 18px rgba(0,0,0,0.12);
  }
  .card--front { left: 50px; top: 150px; background: var(--card-white); }
  .card--back { left: 610px; top: 343px; background: var(--card-dark); }

  .brand {
    position: absolute;
    display: flex;
    align-items: center;
    gap: 10px;
    font-weight: 700;
    letter-spacing: 1px;
    white-space: nowrap;
  }
  .brand__mark { width: 16px; height: 16px; background: var(--red); }
  .card--front .brand { left: 150px; top: 52px; font-size: 28px; color: var(--ink); }
  .card--back .brand { left: 50%; top: 50%; transform: translate(-50%, -50%); font-size: 34px; color: #ffffff; }

  .address {
    position: absolute;
    right: 28px;
    top: 110px;
    text-align: right;
    font-size: 12px;
    line-height: 1.5;
  }
  .divider {
    position: absolute;
    left: 28px;
    right: 28px;
    top: 178px;
    height: 1px;
    background: var(--rule);
  }
  .person { position: absolute; left: 28px; top: 138px; }
  .person__name { color: var(--red); font-weight: 700; font-size: 19px; letter-spacing: 1.5px; text-transform: uppercase; }
  .person__role { font-size: 13px; margin-top: 2px; }

  .contacts { position: absolute; left: 28px; top: 192px; list-style: none; font-size: 12.5px; line-height: 1.7; }
  .contacts li { display: flex; align-items: center; gap: 8px; }
  .contacts svg { width: 11px; height: 11px; fill: var(--red); flex: none; }
</style>
</head>
<body>
  <section class="card card--front">
    <div class="brand"><span class="brand__mark"></span>QEL MOTOR GEAR</div>
    <address class="address">240 W. Harbor Ave.<br>Unit B<br>Fontana, CA 92335</address>
    <div class="person">
      <div class="person__name">Marcus Delane</div>
      <div class="person__role">Manager</div>
    </div>
    <div class="divider"></div>
    <ul class="contacts">
      <li><svg viewBox="0 0 24 24"><path d="M6.6 10.8a15 15 0 0 0 6.6 6.6l2.2-2.2a1 1 0 0 1 1-.25 11.4 11.4 0 0 0 3.6.57 1 1 0 0 1 1 1V20a1 1 0 0 1-1 1A17 17 0 0 1 3 4a1 1 0 0 1 1-1h3.5a1 1 0 0 1 1 1c0 1.25.2 2.45.57 3.57a1 1 0 0 1-.25 1z"/></svg>1-866-555-0142</li>
      <li><svg viewBox="0 0 24 24"><path d="M2 5h20v14H2z M2 5l10 8 10-8" fill="none" stroke="#d71f26" stroke-width="2.5"/></svg>sales@qelmotorgear.com</li>
      <li><svg viewBox="0 0 24 24"><circle cx="12" cy="12" r="10"/></svg>www.qelmotorgear.com</li>
    </ul>
  </section>

  <section class="card card--back">
    <div class="brand"><span class="brand__mark"></span>QEL MOTOR GEAR</div>
  </section>
</body>
</html>
```